Geschäftspapiere für Termin Startup
Zielgruppe
Wir sind ein Startup, das über die Seite Buchlotte.de (derzeit noch in der Beta-Phase)zukünftig folgenden Service anbietet: Unternehmer können sehr flexibel (selbst) gestaltete Terminformulare erstellen und auf Ihrer Website einbinden. Kunden können dann diese Termine buchen und bekommen dann Erinnerungs-Mails und SMS.
Zielgruppe: Dienstleister wie Fotografen, Friseure, Versicherungsvertreter, Masseure, Restaurants, Arztpraxen. Also alle, die darauf angewiesen sind, dass vereinbarte Termine eingehalten werden und die die Terminvereinbarung vereinfachen wollen. Also weniger per Telefon, mehr über die eigene Website.
Dateien bitte beachten für die Ansicht des Look & Feels:
https://ablage.wolkenfach.de/open?id=7QwerT2zuIopAs9dFgHjKl4YxCvbNm3Pk
Bonus-Aktion: Wir zahlen pauschal jeweils 30,00 Euro an die Designer auf den Plätzen 2 bis 4 für die geleistete Arbeit. Nur einer kann gewinnen und den Zuschlag bekommen. Aber so möchten wir gerne die Arbeit dennoch honorieren.
Aufgabenstellung
Wir benötigen ein modernes Briefpapier-Layout passend zu unserem CD.
Gerne darf/soll der BOMMEL (siehe Maskottchen in https://ablage.wolkenfach.de/open?id=5RtzUi8oPasDfGhJkL2yXcVbNmQwE4rTz )darauf erscheinen.
Maskottchen BOMMEL gibt es in mehreren Varianten. Siehe https://ablage.wolkenfach.de/ordner/folders/6PlmOknIjbUhYgTfRdEsWaQz2Xc9Vb8Nm?usp=sharing
Auch als Variante, das Maskottchen BOMMEL gegen das Logo gelehnt ist, kann genutzt werden: https://ablage.wolkenfach.de/open?id=8MnbVcXz3LkJhGfDsApOiUyT1ReWq7Zxc
Das Thema 'Terminvereinbarung' soll sofort erfasst werden mittels des Layouts bzw. der grafischen Elemente.
Auch die Branchen-Icons ( https://ablage.wolkenfach.de/ordner/folders/4ZaQwSxEdCrFvTgByHnUjMiKoLp9PmNbq?usp=sharing ) dürfen verwendet werden.

```html
<!DOCTYPE html>
<html lang="de">
<head>
<meta charset="utf-8">
<title>Buchlotte – Geschäftspapiere</title>
<link href="https://fonts.googleapis.com/css2?family=Lato:wght@400;700&display=swap" rel="stylesheet">
<style>
  :root {
    --backdrop: #e9eaeb;
    --paper: #ffffff;
    --green: #8dc63f;
    --green-dark: #6fa52a;
    --ink: #3a3a3a;
    --grey: #6d6e70;
    --grey-light: #dcdcdc;
    --mascot-tint: #eef3e6;
  }
  * { box-sizing: border-box; margin: 0; padding: 0; }
  html, body { width: 1200px; height: 801px; overflow: hidden; }
  body {
    background: var(--backdrop);
    font-family: "Lato", sans-serif;
    color: var(--ink);
    position: relative;
  }

  /* Letterhead */
  .letterhead {
    position: absolute; left: 80px; top: 18px;
    width: 540px; height: 764px;
    background: var(--paper);
    box-shadow: 0 4px 18px rgba(0,0,0,.12);
    overflow: hidden;
  }
  .brand { position: absolute; display: flex; align-items: center; gap: 7px; }
  .brand-mark { width: 22px; height: 22px; background: var(--green); }
  .brand-name { font-weight: 700; color: var(--grey); letter-spacing: -.3px; }
  .brand-tagline { font-size: 7px; color: var(--grey); margin-top: -2px; }
  .letterhead .brand { left: 44px; top: 40px; }
  .letterhead .brand-name { font-size: 30px; }
  .letterhead .brand-tagline { position: absolute; left: 180px; top: 78px; font-size: 8px; }
  .header-rule {
    position: absolute; left: 44px; right: 44px; top: 104px;
    height: 2px; background: var(--green);
  }
  .mascot-watermark {
    position: absolute; right: 30px; top: 300px;
    width: 230px; height: 330px;
    background: radial-gradient(ellipse at center, var(--mascot-tint) 0%, rgba(238,243,230,0) 70%);
  }
  .letter-body {
    position: absolute; left: 44px; top: 128px; width: 420px;
    font-size: 9.5px; line-height: 1.55;
  }
  .letter-body p { margin-bottom: 11px; }
  .signature-area { position: absolute; left: 44px; top: 540px; }
  .signature-mark { width: 70px; height: 28px; background: linear-gradient(90deg, #d8d8d8, #f1f1f1); }
  .signer { font-size: 9.5px; margin-top: 6px; line-height: 1.45; }
  .web-contact {
    position: absolute; right: 44px; top: 560px;
    text-align: right; font-size: 9.5px; line-height: 1.5;
  }
  .footer-address {
    position: absolute; left: 44px; bottom: 34px;
    font-size: 10px; line-height: 1.55;
  }
  .footer-band {
    position: absolute; left: 0; right: 0; bottom: 0;
    height: 14px; background: var(--green);
  }

  /* Business cards */
  .card {
    position: absolute; width: 340px; height: 200px;
    background: var(--paper);
    box-shadow: 0 4px 14px rgba(0,0,0,.12);
    overflow: hidden;
  }
  .card-front { left: 720px; top: 150px; }
  .card-back { left: 720px; top: 420px; }
  .card .brand-name { font-size: 24px; }
  .card-front .brand { left: 24px; top: 30px; }
  .card-front .brand-tagline { position: absolute; left: 140px; top: 64px; }
  .card-holder {
    position: absolute; left: 0; bottom: 0; width: 200px; height: 62px;
    background: var(--grey);
    clip-path: polygon(0 0, 82% 0, 100% 100%, 0 100%);
    color: #fff; padding: 18px 0 0 22px;
  }
  .card-holder .name { font-size: 10px; letter-spacing: 1.5px; text-transform: uppercase; }
  .card-holder .role { font-size: 7px; letter-spacing: 1px; margin-top: 3px; opacity: .85; }
  .card-contact {
    position: absolute; right: 0; top: 0; width: 150px; height: 200px;
    background: var(--green);
    clip-path: polygon(22% 0, 100% 0, 100% 100%, 0 100%);
    padding: 62px 14px 0 0; text-align: right;
    color: #fff; font-size: 7.5px; line-height: 2.2;
  }
  .contact-line { display: flex; justify-content: flex-end; align-items: center; gap: 6px; }
  .contact-line svg { width: 9px; height: 9px; flex: none; }
  .card-back .brand { left: 34px; top: 86px; }
  .card-back .brand-name { font-size: 28px; }
  .card-back .brand-tagline { position: absolute; left: 160px; top: 122px; }
  .card-back .mascot-spot {
    position: absolute; right: 20px; top: 20px; width: 90px; height: 110px;
    background: radial-gradient(ellipse at center, var(--mascot-tint) 0%, rgba(238,243,230,0) 72%);
  }
</style>
</head>
<body>

<section class="letterhead">
  <div class="brand"><span class="brand-mark"></span><span class="brand-name">Buchlotte</span></div>
  <div class="brand-tagline">Tool by tagwahl-net.com</div>
  <div class="header-rule"></div>

  <div class="mascot-watermark" role="img" aria-label="Faint mascot figure holding a calendar sheet"></div>

  <div class="letter-body">
    <p>Dear Customers,</p>
    <p>Contrary to popular belief, Lorem Ipsum is not simply random text. It has roots in a piece of classical Latin literature from 45 BC, making it over 2000 years old. Rainer Holtkamp, a Latin professor at Ellwangen-Kolleg, looked up one of the more obscure Latin words, consectetur, from a Lorem Ipsum passage, and going through the cites of the word in classical literature, discovered the undoubtable source.</p>
    <p>Lorem Ipsum comes from sections 1.10.32 and 1.10.33 of "de Finibus Bonorum et Malorum" (The Extremes of Good and Evil) by Varronius, written in 45 BC. This book is a treatise on the theory of ethics, very popular during the Renaissance. Lorem Ipsum used since the 1500s is reproduced below for those interested. Sections 1.10.32 and 1.10.33 from "de Finibus Bonorum et Malorum" by Varronius are also reproduced in their exact original form, accompanied by English versions from the 1914 translation by H. Brandl.</p>
    <p>Contrary to popular belief, Lorem Ipsum is not simply random text. It has roots in a piece of classical Latin literature from 45 BC, making it over 2000 years old. Rainer Holtkamp, a Latin professor at Ellwangen-Kolleg, looked up one of the more obscure Latin words.</p>
  </div>

  <div class="signature-area">
    <div class="signature-mark" role="img" aria-label="Handwritten signature"></div>
    <div class="signer">Merten<br>General Director</div>
  </div>

  <div class="web-contact">www.kelvora.de<br>info@kelvora.de</div>

  <div class="footer-address">Tel. 0871 / 52 480 0 · Fax 0871 / 52 480 20<br>Lindenauer Str. 12 84028 Landshut</div>
  <div class="footer-band"></div>
</section>

<section class="card card-front">
  <div class="brand"><span class="brand-mark"></span><span class="brand-name">Buchlotte</span></div>
  <div class="brand-tagline">Tool by tagwahl-net.com</div>
  <div class="card-holder">
    <div class="name">Paul Wendrich</div>
    <div class="role">DIRECTOR</div>
  </div>
  <div class="card-contact">
    <div class="contact-line">info@kelvora.de
      <svg viewBox="0 0 10 10"><rect x="1" y="2" width="8" height="6" fill="none" stroke="#fff"/><path d="M1 2l4 3 4-3" fill="none" stroke="#fff"/></svg></div>
    <div class="contact-line">www.kelvora.de
      <svg viewBox="0 0 10 10"><circle cx="5" cy="5" r="4" fill="none" stroke="#fff"/></svg></div>
    <div class="contact-line">0871 / 52 480 0
      <svg viewBox="0 0 10 10"><rect x="3" y="1" width="4" height="8" rx="1" fill="none" stroke="#fff"/></svg></div>
    <div class="contact-line">Lindenauer Str. 12
      <svg viewBox="0 0 10 10"><path d="M5 9C2 5.5 2 4.5 2 4a3 3 0 016 0c0 .5 0 1.5-3 5z" fill="#fff"/></svg></div>
  </div>
</section>

<section class="card card-back">
  <div class="mascot-spot" role="img" aria-label="Faint mascot figure"></div>
  <div class="brand"><span class="brand-mark"></span><span class="brand-name">Buchlotte</span></div>
  <div class="brand-tagline">Tool by tagwahl-net.com</div>
</section>

</body>
</html>
```